Business card design for new eCommerce site focusing on integrity and strong businsess tactics

We need a business card that will stand out and be memorable. Something with color that matches our company logo colors. Think high end version of Pactivo. There are 2 logos provided. The parent company is called Amber Ledge Partners and we are presenting a new and very exciting eCommerce site called BrightHarborTrade.example.

Target Market(s)

Our target markets are in the Activities, Food and Beverage, Health and Beauty

Industry/Entity Type

Marketing

Contact Information for Business Card

We have 4 members that need cards...I will provide all info to the winner of the design contest
Business Address is
4870 West 63rd Avenue, Suite C207
Phoenix AZ 85731

Font styles to use
Serif
Sans Serif

Colors

Designer to choose colors to be used in the design.

Requirements
Must have
• The card must be memorable...should be unique in design but must exude integrity and be playful .
• I have provided several colors or our parent company...please feel free to use which ever
Nice to have
• I will leave this up to you. Feel free to use other images of your choosing that wraps around our client.....Activities, Dining, Health, Beauty
Should not have
• just dont be boring

```html
<!DOCTYPE html>
<html lang="en">
<head>
<meta charset="utf-8">
<title>Amber Ledge Partners – Business Cards</title>
<link href="https://fonts.googleapis.com/css2?family=Roboto:wght@400;500;700&family=Roboto+Condensed:wght@700&display=swap" rel="stylesheet">
<style>
  :root {
    --backdrop: #2c2c2c;
    --card: #f7f7f7;
    --leaf-green: #8dc63f;
    --lime: #a3c940;
    --ocean: #2b7db3;
    --ink-grey: #5b5b5b;
    --white: #ffffff;
  }
  * { box-sizing: border-box; margin: 0; padding: 0; }
  html, body { width: 1200px; height: 960px; overflow: hidden; }
  body {
    background: var(--backdrop);
    font-family: "Roboto", Arial, sans-serif;
    position: relative;
  }
  .card {
    position: absolute;
    width: 598px;
    height: 342px;
    border-radius: 18px;
    background: var(--card);
    overflow: hidden;
  }
  .card--front { left: 320px; top: 100px; }
  .front-mark {
    position: absolute;
    left: 229px; top: 78px;
    width: 140px; height: 140px;
    border-radius: 50%;
    background: var(--lime);
    box-shadow: 0 0 0 3px var(--card), 0 0 0 5px var(--lime);
  }
  .front-name {
    position: absolute;
    left: 0; right: 0; top: 232px;
    text-align: center;
    font-size: 33px;
    font-weight: 700;
    color: var(--lime);
    letter-spacing: -0.3px;
  }
  .card--back { left: 320px; top: 493px; }
  .back-wave { position: absolute; inset: 0; }
  .holder {
    position: absolute;
    right: 35px; top: 30px;
    text-align: right;
  }
  .holder-name {
    font-family: "Roboto Condensed", Arial, sans-serif;
    font-size: 21px;
    font-weight: 700;
    color: var(--leaf-green);
    line-height: 1.1;
  }
  .holder-title {
    font-size: 14px;
    font-weight: 500;
    color: var(--white);
    margin-top: 2px;
  }
  .address {
    position: absolute;
    right: 35px; top: 192px;
    text-align: right;
    font-size: 14px;
    font-style: normal;
    line-height: 19px;
    color: var(--white);
  }
  .contacts {
    position: absolute;
    right: 35px; top: 238px;
    list-style: none;
    text-align: right;
    font-size: 14px;
    line-height: 19px;
    color: var(--white);
  }
  .contacts li { display: flex; justify-content: flex-end; align-items: center; gap: 6px; }
  .contacts svg { width: 12px; height: 12px; fill: var(--leaf-green); flex: none; }
  .brand {
    position: absolute;
    left: 24px; top: 216px;
  }
  .brand-row { display: flex; align-items: center; gap: 8px; }
  .brand-dot {
    width: 30px; height: 30px;
    border-radius: 50%;
    background: var(--ocean);
  }
  .brand-name {
    font-size: 19px;
    font-weight: 500;
    color: var(--leaf-green);
  }
  .brand-tagline {
    margin: 6px 0 0 38px;
    font-size: 11px;
    color: var(--ink-grey);
    letter-spacing: 0.6px;
  }
</style>
</head>
<body>

  <section class="card card--front" aria-label="Card front">
    <div class="front-mark"></div>
    <p class="front-name">Amber Ledge Partners</p>
  </section>

  <section class="card card--back" aria-label="Card back">
    <svg class="back-wave" viewBox="0 0 598 342" aria-hidden="true">
      <path d="M300,0 C238,40 238,110 288,180 C333,245 308,300 273,342 L283,342 C318,300 343,245 298,180 C248,110 248,40 310,0 Z" fill="var(--leaf-green)"/>
      <path d="M312,0 C250,40 250,110 300,180 C345,245 320,300 285,342 L598,342 L598,0 Z" fill="var(--ocean)"/>
    </svg>

    <div class="holder">
      <p class="holder-name">DANA WHITFIELD</p>
      <p class="holder-title">CEO/FOUNDER</p>
    </div>

    <address class="address">
      4870 West 63rd Avenue<br>
      Suite C207, Phoenix AZ 85731
    </address>

    <ul class="contacts">
      <li>555 014 2738
        <svg viewBox="0 0 24 24"><path d="M6.6 10.8a15 15 0 0 0 6.6 6.6l2.2-2.2c.3-.3.7-.4 1-.2 1.1.4 2.3.6 3.6.6.6 0 1 .4 1 1V20c0 .6-.4 1-1 1A17 17 0 0 1 3 4c0-.6.4-1 1-1h3.5c.6 0 1 .4 1 1 0 1.3.2 2.5.6 3.6.1.3 0 .7-.2 1z"/></svg>
      </li>
      <li>555 019 6641
        <svg viewBox="0 0 24 24"><path d="M7 1h10a2 2 0 0 1 2 2v18a2 2 0 0 1-2 2H7a2 2 0 0 1-2-2V3a2 2 0 0 1 2-2zm0 3v14h10V4zm5 15.5a1 1 0 1 0 0 2 1 1 0 0 0 0-2z"/></svg>
      </li>
      <li>dana@brightharbortrade.example
        <svg viewBox="0 0 24 24"><path d="M2 5h20v14H2zm2 2v.5l8 5 8-5V7zm0 2.8V17h16V9.8l-8 5z"/></svg>
      </li>
      <li>www.brightharbortrade.example
        <svg viewBox="0 0 24 24"><path d="M12 2a10 10 0 1 0 0 20 10 10 0 0 0 0-20zm6.9 6h-3a15 15 0 0 0-1.3-3.9A8 8 0 0 1 18.9 8zM12 4c.8 1.2 1.5 2.5 1.9 4h-3.8c.4-1.5 1.1-2.8 1.9-4zM4.3 14a8 8 0 0 1 0-4h3.4a16 16 0 0 0 0 4zm.8 2h3a15 15 0 0 0 1.3 3.9A8 8 0 0 1 5.1 16zm3-8h-3a8 8 0 0 1 4.3-3.9C8.8 5.3 8.4 6.6 8.1 8zM12 20c-.8-1.2-1.5-2.5-1.9-4h3.8c-.4 1.5-1.1 2.8-1.9 4zm2.3-6H9.7a14 14 0 0 1 0-4h4.6a14 14 0 0 1 0 4zm.3 5.9c.6-1.2 1-2.5 1.3-3.9h3a8 8 0 0 1-4.3 3.9zm1.7-5.9a16 16 0 0 0 0-4h3.4a8 8 0 0 1 0 4z"/></svg>
      </li>
    </ul>

    <div class="brand">
      <div class="brand-row">
        <span class="brand-dot"></span>
        <span class="brand-name">BrightHarborTrade.example</span>
      </div>
      <p class="brand-tagline">Outings-Meals-Wellness-Style</p>
    </div>
  </section>

</body>
</html>
```